Striking new Advert required for Commercial Real Estate Agency

We need a a NEW newspaper advertisement for the marketing of a large commercial property (a Backpackers lodge)

Dimensions are to be width of 101mm and height of 100mm (10cms)

Our key design statement for this advert is clean, modern and minimalist design, with accents of 'HOT PINK' colour to remove it from looking too boring, perhaps in the area of the contact icons. The heirachy of the advert is outlined in the attached ADVERTISEMENT TEXT FILE.

Our company name is THE HARBOURLINE COLLECTIVE, and we want our brand to appear professional yet classy in it's design style (sort of like an advertising or design agency)

We have two logo options below, one more square in its layout (which we prefer) and the other more rectangular, which may be better suited for the layout. We are not adverse to the logo being reversed (white text on black), along with other key element areas such as the main advert heading and the "FOR SALE" part, and think this would be a good option.
There are two photos attached to be included in the advert.

We have attached an example of an old advert that we did, which we DID NOT LIKE, and which was for a smaller width than the one we need (it is only 65% of the width of this one). WE have also atached a file showing layout of some of our competitors adverts, which we dont think are too good either.

We are really open for ideas, but have time pressures, so please come back with any questions as soon as you can, if needed.

Thank you
Updates

Thank you for the great and diverse designs. There are a few standout options, but one style that we prefer most.

Target Market(s)

We are wanting this newspaper advertisement to attract interest from real estat e developers, investors and motel/lodge owners, along with other high nett worth individuals

Industry/Entity Type

Real Estate

Font styles to use
Serif
Sans Serif

Colors
1b1b1b
a54499
474747
fbfbfb

Requirements
Must have
• Clean modern look, predominantly monochromatic or black and white, with the hot pink accent somewhere, as mentioned above.
• All the contents of the TEXT provided, perhaps with additional space to add a little more if needed, Please advise if you think we dont have enough space for all of the TEXT
Should not have
• Script like fonts
• Cartoonish characters
• a 'cheap' look

```html
<!DOCTYPE html>
<html lang="en">
<head>
<meta charset="utf-8">
<title>For Sale – Mount Victoria Land Grab</title>
<link href="https://fonts.googleapis.com/css2?family=Montserrat:wght@300;400;500;700;800&display=swap" rel="stylesheet">
<style>
  :root {
    --ink: #1b1b1b;
    --panel: rgba(38, 38, 44, 0.86);
    --band: rgba(27, 27, 27, 0.72);
    --pink: #a54499;
    --grey: #474747;
    --paper: #fbfbfb;
    --white: #ffffff;
  }
  * { margin: 0; padding: 0; box-sizing: border-box; }
  html, body { width: 1200px; height: 1200px; overflow: hidden; background: var(--white); }
  body { font-family: "Montserrat", Arial, sans-serif; color: var(--paper); }

  .advert {
    position: absolute; left: 120px; top: 128px;
    width: 956px; height: 944px; overflow: hidden;
  }
  .property-photo {
    position: absolute; inset: 0;
    background: linear-gradient(180deg, #4c82cc 0%, #9fb9dc 18%, #e4e4e0 34%, #d6d5cf 60%, #b9b6ad 70%, #4d5c3a 82%, #2f3d26 100%);
  }
  .info-panel {
    position: absolute; left: 0; top: 0; width: 392px; height: 100%;
    background: var(--panel);
  }
  .contact-band {
    position: absolute; left: 0; top: 666px; width: 100%; height: 278px;
    background: var(--band);
  }

  .headline {
    position: absolute; left: 28px; top: 60px;
    font-weight: 800; font-size: 64px; letter-spacing: 0; line-height: 1;
    color: var(--white); white-space: nowrap;
  }
  .subhead {
    position: absolute; left: 18px; top: 142px;
    font-weight: 300; font-size: 29px; letter-spacing: -0.5px;
    color: var(--pink); white-space: nowrap;
  }
  .subhead-rule {
    position: absolute; left: 16px; top: 182px; width: 358px; height: 2px;
    background: #8a8a8e;
  }
  .location-pin { position: absolute; left: 38px; top: 200px; width: 56px; height: 80px; }
  .address {
    position: absolute; left: 128px; top: 202px;
    font-size: 21px; line-height: 27.5px; font-weight: 400; color: var(--paper);
    white-space: nowrap;
  }

  .description {
    position: absolute; left: 20px; top: 312px; width: 372px;
    font-size: 16px; line-height: 20px; color: var(--paper); white-space: nowrap;
  }
  .description ul { list-style: none; }
  .description li { position: relative; padding-left: 14px; }
  .description li::before {
    content: "•"; position: absolute; left: 0; color: var(--pink);
  }
  .description sup { font-size: 9px; line-height: 0; }
  .tender { font-weight: 700; }

  .contact {
    position: absolute; left: 17px; top: 690px;
    font-size: 23px; line-height: 1; white-space: nowrap;
  }
  .contact-label { font-weight: 400; font-size: 25px; color: var(--pink); margin-bottom: 12px; }
  .agent-name { font-weight: 700; margin-bottom: 12px; }
  .contact-line { display: flex; align-items: center; gap: 3px; margin-bottom: 12px; font-weight: 400; }
  .contact-line svg { width: 18px; height: 22px; }
  .contact-web { font-weight: 700; font-size: 22px; margin-bottom: 10px; }

  .brand-name {
    position: absolute; left: 540px; top: 768px;
    font-weight: 400; font-size: 32px; line-height: 44px; letter-spacing: 1px;
    color: var(--white); white-space: nowrap;
  }
</style>
</head>
<body>
<div class="advert">
  <div class="property-photo" role="img" aria-label="Photo of the white weatherboard two-storey lodge with lilac window frames, balconies and a fire escape under blue sky, garden shrubs in front"></div>
  <div class="info-panel"></div>
  <div class="contact-band"></div>

  <h1 class="headline">FOR SALE</h1>
  <h2 class="subhead">Mount Victoria Land Grab</h2>
  <div class="subhead-rule"></div>

  <svg class="location-pin" viewBox="0 0 56 80" aria-hidden="true">
    <path d="M28 2C13 2 2 13 2 27c0 17 26 43 26 43s26-26 26-43C54 13 43 2 28 2z" fill="#a54499"/>
    <circle cx="28" cy="27" r="10" fill="none" stroke="#2a2a2f" stroke-width="5"/>
    <ellipse cx="28" cy="76" rx="14" ry="3" fill="#a54499"/>
  </svg>
  <p class="address">Marlowe’s Lodge,<br>27 Kestrel Street,<br>Mount Victoria</p>

  <div class="description">
    <p>This Old Beauty has served many,<br>and is now ripe for development.<br>One of Mt Vic’s largest land areas,<br>now offered with vacant possession,<br>with key details being:</p>
    <ul>
      <li>Large Land area of 2076m<sup>2</sup> with<br>elevated sunny position and great<br>outlook + access from Tarrant Street</li>
      <li>Existing Backpackers Lodge of<br>970m<sup>2</sup> providing multiple rooms<br>with amenity areas</li>
      <li>Four adjacent sites also available,<br>taking total land area to 4452m<sup>2</sup>, an<br>unprecedented Land</li>
    </ul>
    <p>Offering in this popular city fringe<br>location</p>
    <p class="tender">Now Selling by Closed Tender</p>
  </div>

  <div class="contact">
    <p class="contact-label">Contact the Sole Agent</p>
    <p class="agent-name">Daniel Whitmore</p>
    <p class="contact-line">
      <svg viewBox="0 0 18 22" aria-hidden="true"><path d="M4 2l3 0 2 5-2 2c1 3 3 5 5 6l2-2 4 2v3c0 1-1 2-2 2C8 20 2 12 2 4c0-1 1-2 2-2z" fill="none" stroke="#fbfbfb" stroke-width="2"/></svg>
      (04) 555 0142
    </p>
    <p class="contact-line">
      <svg viewBox="0 0 18 22" aria-hidden="true"><rect x="3" y="2" width="12" height="19" rx="2" fill="none" stroke="#fbfbfb" stroke-width="2"/></svg>
      (021) 555 018
    </p>
    <p class="contact-web">daniel@harbourline.co.nz</p>
    <p class="contact-web">www.harbourline.co.nz</p>
  </div>

  <p class="brand-name">THE HARBOURLINE<br>COLLECTIVE</p>
</div>
</body>
</html>
```